Bright Harbor Web Design & Marketing

Will award a 2nd place prize of $100.00 if someone can come up with a logo to match this design!
Updates

Okay, I'm really looking to see some better designs here. What do you think will bring the best designs out? Please remember with all future submissions I'm looking for a cartoon style / illustrator style website. I'm not sure what the technical term is for it, so I uploaded some images in the brief.

Target Market(s)

Small Business Owners

Industry/Entity Type

Marketing

Logo Text

BrightHarbor.com

Number of Pages Required

1 page

Colors

Designer to choose colors to be used in the design.

Requirements
Must have
• Logo should say BrightHarbor.com I would like more than just a text logo. I want some sort of cool custom graphic / icon with it that will look nice on shirts/hats/etc

```html
<!DOCTYPE html>
<html lang="en">
<head>
<meta charset="utf-8">
<title>BrightHarbor.com — Web Design & Marketing</title>
<link href="https://fonts.googleapis.com/css2?family=Cinzel:wght@400;700&family=Open+Sans:wght@400;600;700;800&family=Lora:wght@400;700&display=swap" rel="stylesheet">
<style>
:root{
  --orange:#f47c20;
  --orange-dark:#d9641a;
  --ink:#1c1c1c;
  --header:#151515;
  --sky:#5ec4d4;
  --night:#1d2a36;
  --navy:#4b5784;
  --mist:#dde9f3;
  --cream:#f5f2ea;
  --grey-btn:#5b5b5b;
  --text:#444;
  --light:#fff;
  --footer:#101823;
  --footer-bar:#0d2c4f;
  --wood:#b98a58;
}
*{box-sizing:border-box;margin:0;padding:0}
html,body{width:1200px;height:4737px;overflow:hidden}
body{position:relative;font-family:"Lora",Georgia,serif;color:var(--text);background:#fff}
section,header,footer{position:absolute;left:0;width:1200px}
.section-title{font-family:"Cinzel",Georgia,serif;font-size:32px;letter-spacing:2px;text-align:center;color:var(--ink);position:absolute;left:0;width:1200px}
.lede{position:absolute;left:150px;width:900px;text-align:center;font-size:13px;line-height:20px}
.placeholder{position:absolute}

/* header */
.site-header{top:0;height:88px;background:var(--header)}
.brand{position:absolute;left:132px;top:24px;display:flex;align-items:center;gap:10px;font-family:"Open Sans",sans-serif;font-weight:800;font-size:24px;color:var(--light)}
.brand-mark{width:34px;height:34px;border-radius:50%;background:var(--orange)}
.main-nav{position:absolute;left:530px;top:0;display:flex;height:88px}
.main-nav a{display:flex;flex-direction:column;align-items:center;justify-content:center;gap:8px;padding:0 18px;color:var(--light);text-decoration:none;font-family:"Open Sans",sans-serif;font-size:13px;font-weight:600;text-transform:uppercase}
.main-nav a.active{background:var(--orange)}
.main-nav svg{width:22px;height:22px}

/* hero */
.hero{top:88px;height:506px;background:var(--sky)}
.hero-art{left:70px;top:30px;width:470px;height:460px;background:radial-gradient(circle at 50% 45%,#e8553d 0,#3b3b4a 35%,transparent 62%)}
.hero-title{position:absolute;right:135px;top:130px;text-align:right;font-family:"Open Sans",sans-serif;font-weight:800;font-size:40px;line-height:52px;color:var(--ink)}
.hero-title em{font-style:normal;color:var(--light)}
.btn{display:inline-flex;align-items:center;gap:8px;font-family:"Lora",serif;font-size:16px;color:var(--light);padding:9px 16px;border-radius:3px}
.btn-grey{background:var(--grey-btn)}
.btn-orange{background:var(--orange)}
.hero .btn{position:absolute;right:135px;top:370px}
.slider-arrow{position:absolute;top:268px;width:22px;height:30px;background:#333}
.slider-arrow.left{left:0}.slider-arrow.right{right:0}

/* about */
.about{top:594px;height:328px}
.about .section-title{top:50px}
.about .section-title span{color:var(--orange)}
.about .lede{top:112px}
.about-actions{position:absolute;top:222px;left:0;width:1200px;display:flex;justify-content:center;gap:14px}

/* services */
.services{top:922px;height:752px;background:linear-gradient(180deg,#16222c,#26384a 60%,#1a2733)}
.services .section-title{top:42px;color:var(--light)}
.services .lede{top:92px;color:#ddd}
.service-map{position:absolute;left:0;top:0}
.service-hub{left:530px;top:330px;width:140px;height:140px;border-radius:50%;background:radial-gradient(#2b3b4b,#1d2a36)}
.service-label{position:absolute;width:170px;font-size:11px;line-height:14px;color:#ddd}
.service-label b{display:block;font-family:"Open Sans",sans-serif;font-size:12px;color:#ffd54a}

/* plans */
.plans{top:1674px;height:663px}
.plans .section-title{top:50px}
.wood{left:0;top:347px;width:1200px;height:316px;background:linear-gradient(180deg,#c99c6a,var(--wood) 40%,#8e6338)}
.plan{position:absolute;top:136px;width:200px;height:464px;background:#fff;border-top:5px solid var(--orange);box-shadow:0 2px 8px rgba(0,0,0,.25);text-align:center;font-family:"Open Sans",sans-serif}
.plan-icon{width:50px;height:50px;border-radius:50%;margin:22px auto 10px;background:#eef3f7;display:flex;align-items:center;justify-content:center}
.plan h3{font-size:16px;font-weight:600;color:var(--ink);padding-bottom:14px;border-bottom:1px solid #eee}
.plan .from{font-size:10px;color:#999;margin-top:12px}
.plan .price{font-size:40px;color:var(--ink);font-weight:400}
.plan .price sup{font-size:16px}.plan .price small{font-size:14px}
.plan ul{list-style:none;text-align:left;padding:10px 16px;border-top:1px solid #eee;margin-top:10px}
.plan li{font-family:"Lora",serif;font-size:11px;white-space:nowrap;padding:7px 0 7px 14px;border-bottom:1px solid #f0f0f0;position:relative}
.plan li:before{content:"›";position:absolute;left:2px;color:#999}
.plan .start{display:inline-block;width:120px;padding:7px 0;color:#fff;font-size:12px;margin-top:14px;background:var(--grey-btn)}
.plan.featured .start{background:var(--orange)}
.plan .more{display:block;font-size:10px;margin-top:6px;color:#555}

/* video */
.video{top:2337px;height:505px}
.video .section-title{top:62px}
.video-art{left:332px;top:110px;width:505px;height:379px;background:linear-gradient(135deg,#e8d3c2,#f4f4f4 30%,#4b5784 45%,#4b5784 70%,#e1c5b0)}
.play{position:absolute;left:560px;top:270px;width:80px;height:80px}

/* band */
.band{top:2842px;height:88px;background:var(--navy);color:var(--light);text-align:center;font-family:"Cinzel",serif;font-size:17px;line-height:26px;padding-top:18px;letter-spacing:1px}

/* clients */
.clients{top:2930px;height:291px;background:var(--cream)}
.clients .section-title{top:40px}
.clients .lede{top:96px}
.client-row{position:absolute;top:176px;left:140px;width:920px;display:flex;justify-content:space-between;align-items:center;font-family:"Open Sans",sans-serif;font-weight:700;font-size:16px;color:#222}
.client-row span{display:flex;align-items:center;gap:6px}
.client-row i{width:14px;height:14px;border-radius:50%;background:#222;display:inline-block}
.client-arrow{position:absolute;top:178px;font-size:22px;color:#888;font-family:"Open Sans",sans-serif}

/* why */
.why{top:3221px;height:505px;background:var(--mist)}
.why .section-title{top:46px}
.why .lede{top:100px}
.why-emblem{left:545px;top:158px;width:110px;height:110px;border-radius:18px;background:radial-gradient(#3a8fd0,#1b5f9c)}
.why-item{position:absolute;width:240px;font-size:12px;line-height:16px;text-align:center}
.why-item b{display:block;font-family:"Open Sans",sans-serif;font-size:13px;font-weight:700;color:var(--orange)}
.why-item b.blue{color:#1b5f9c}

/* team */
.team{top:3726px;height:332px}
.team .section-title{top:50px}
.team .lede{top:108px}
.member{position:absolute;top:160px;width:430px;height:150px;border:1px solid #e3e3e3;background:#fff;padding:14px 16px;font-size:12px;line-height:16px}
.member .photo{position:absolute;left:16px;top:14px;width:64px;height:64px;background:linear-gradient(#c9d3dc,#8a99a8)}
.member h4{margin-left:80px;font-family:"Open Sans",sans-serif;font-size:13px;color:var(--ink);margin-top:6px}
.member .role{margin-left:80px;color:var(--orange);font-size:12px}
.member p.bio{margin-top:28px}

/* inquiry */
.inquiry{top:4058px;height:379px}
.inquiry-art{left:0;top:10px;width:470px;height:369px;background:linear-gradient(135deg,#f1f1f1,#d7dde2 55%,#b9c2ca)}
.inquiry .section-title{top:42px}
.form{position:absolute;left:490px;top:110px;width:520px;font-family:"Open Sans",sans-serif;font-size:11px;color:#666}
.form .row{display:flex;gap:20px;margin-bottom:12px}
.field{flex:1;border-bottom:1px solid #ccc;padding:6px 0}
.field.area{height:74px;border:1px solid #ccc;padding:6px}
.submit{display:inline-block;margin-top:14px;background:#1b6fb8;color:#fff;font-size:11px;padding:8px 18px}

/* footer */
.site-footer{top:4437px;height:300px;background:linear-gradient(180deg,#233243,var(--footer))}
.foot-col{position:absolute;top:34px;color:#ddd;font-size:12px;line-height:20px}
.foot-col h5{font-family:"Cinzel",serif;font-size:14px;color:#fff;margin-bottom:8px;font-weight:400}
.foot-col h5 span{color:var(--orange)}
.foot-col ul{list-style:none}
.foot-col li:before{content:"› ";color:var(--orange)}
.news-field{width:210px;height:26px;background:#fff;margin:8px 0;color:#888;font-family:"Open Sans",sans-serif;font-size:10px;padding:6px}
.subscribe{display:inline-block;background:#1b6fb8;color:#fff;padding:4px 14px;font-size:12px}
.foot-mark{position:absolute;left:930px;top:40px;width:140px;height:140px;border-radius:50%;background:rgba(255,255,255,.12)}
.foot-bar{position:absolute;left:0;top:268px;width:1200px;height:32px;background:var(--footer-bar);color:#ccc;font-size:11px;font-family:"Open Sans",sans-serif;padding:9px 148px;display:flex;justify-content:space-between}
</style>
</head>
<body>

<header class="site-header">
  <div class="brand"><span class="brand-mark"></span>BrightHarbor.com</div>
  <nav class="main-nav">
    <a class="active" href="#"><svg viewBox="0 0 24 24" fill="#fff"><path d="M12 3 2 12h3v9h5v-6h4v6h5v-9h3z"/></svg>Home</a>
    <a href="#"><svg viewBox="0 0 24 24" fill="#fff"><rect x="3" y="5" width="18" height="14" rx="2"/></svg>Services &amp; Pricing</a>
    <a href="#"><svg viewBox="0 0 24 24" fill="#fff"><circle cx="8" cy="8" r="4"/><circle cx="16" cy="8" r="4"/><path d="M1 21c0-5 14-5 14 0zM9 21c0-5 14-5 14 0z"/></svg>Our Team</a>
    <a href="#"><svg viewBox="0 0 24 24" fill="#fff"><circle cx="12" cy="8" r="4"/><path d="M4 22c0-7 16-7 16 0z"/></svg>Clients</a>
    <a href="#"><svg viewBox="0 0 24 24" fill="#fff"><path d="M2 5h20v14H2zM2 5l10 8 10-8" stroke="#151515" stroke-width="1.5"/></svg>Contact Us</a>
  </nav>
</header>

<section class="hero">
  <div class="placeholder hero-art" role="img" aria-label="Cartoon superhero flying with a shopping bag"></div>
  <h1 class="hero-title">The Design &amp; Marketing<br>Team That Always Puts<br><em>Bright Harbor</em> Before<br>Profits</h1>
  <span class="btn btn-grey">☎ Call Us Today</span>
  <span class="slider-arrow left"></span><span class="slider-arrow right"></span>
</section>

<section class="about">
  <h2 class="section-title">About <span>BrightHarbor</span>.com</h2>
  <p class="lede">We believe that honesty and integrity come before personal profit. We are a family owned and operated company. Our parents raised us to take care of each other and that is exactly what we've done. We treat each of our clients with the same loyalty and respect that we give each other.<br><br>We are not looking to have hundreds and hundreds of clients. We are looking to expand our family with a handful of like-minded individuals. Companies who take pride in their work and their customers. We want to build mutually beneficial, lucrative, and long term partnerships.</p>
  <div class="about-actions"><span class="btn btn-orange">Read More</span><span class="btn btn-grey">☎ Call Us Today</span></div>
</section>

<section class="services">
  <h2 class="section-title">Services We Provide</h2>
  <p class="lede">Lorem ipsum dolor sit amet, consectetuer adipiscing elit, sed diam nonummy nibh euismod tincidunt ut laoreet dolore magna aliquam erat volutpat. Ut wisi enim ad minim veniam, quis nostrud exerci.</p>
  <svg class="service-map" width="1200" height="752" viewBox="0 0 1200 752">
    <g stroke="#8aa" stroke-width="1.5" fill="none">
      <circle cx="600" cy="400" r="200" stroke-dasharray="4 4"/>
      <line x1="600" y1="400" x2="560" y2="220"/><line x1="600" y1="400" x2="650" y2="210"/>
      <line x1="600" y1="400" x2="755" y2="280"/><line x1="600" y1="400" x2="760" y2="430"/>
      <line x1="600" y1="400" x2="690" y2="540"/><line x1="600" y1="400" x2="560" y2="585"/>
      <line x1="600" y1="400" x2="410" y2="480"/><line x1="600" y1="400" x2="420" y2="350"/>
    </g>
    <g font-family="Open Sans, sans-serif" font-weight="700" font-size="14" fill="#fff" text-anchor="middle">
      <circle cx="560" cy="220" r="30" fill="#f4b400"/>
      <circle cx="650" cy="210" r="32" fill="#29b6f6"/>
      <circle cx="755" cy="280" r="32" fill="#8bc34a"/>
      <circle cx="760" cy="430" r="32" fill="#ab47bc"/>
      <circle cx="690" cy="540" r="32" fill="#ef5350"/>
      <circle cx="560" cy="585" r="32" fill="#26c6da"/>
      <circle cx="410" cy="480" r="32" fill="#cddc39"/>
      <circle cx="420" cy="350" r="32" fill="#26a69a"/>
      <circle cx="590" cy="252" r="11" fill="#fff"/><text x="590" y="257" fill="#333">1</text>
      <circle cx="700" cy="240" r="11" fill="#fff"/><text x="700" y="245" fill="#333">2</text>
      <circle cx="785" cy="320" r="11" fill="#fff"/><text x="785" y="325" fill="#333">3</text>
      <circle cx="735" cy="490" r="11" fill="#fff"/><text x="735" y="495" fill="#333">4</text>
      <circle cx="640" cy="560" r="11" fill="#fff"/><text x="640" y="565" fill="#333">5</text>
      <circle cx="510" cy="590" r="11" fill="#fff"/><text x="510" y="595" fill="#333">6</text>
      <circle cx="380" cy="450" r="11" fill="#fff"/><text x="380" y="455" fill="#333">7</text>
      <circle cx="390" cy="380" r="11" fill="#fff"/><text x="390" y="385" fill="#333">8</text>
    </g>
  </svg>
  <div class="placeholder service-hub" role="img" aria-label="Central service emblem illustration"></div>
  <div class="service-label" style="left:340px;top:160px"><b>Consulting Service</b>Duis autem vel eum iriure dolor in hendrerit vulputate velit.</div>
  <div class="service-label" style="left:730px;top:150px"><b>Website Design &amp; Management</b>Duis autem vel eum iriure dolor in hendrerit vulputate velit.</div>
  <div class="service-label" style="left:830px;top:240px"><b>Logo Design &amp; Branding Materials</b>Duis autem vel eum iriure dolor in hendrerit vulputate.</div>
  <div class="service-label" style="left:830px;top:380px"><b>Video Editing Design &amp; Production</b>Duis autem vel eum iriure dolor in hendrerit.</div>
  <div class="service-label" style="left:760px;top:520px"><b>Lead Management</b>Duis autem vel eum iriure dolor in hendrerit.</div>
  <div class="service-label" style="left:600px;top:632px"><b>Search Engine Optimization</b>Duis autem vel eum iriure dolor in hendrerit.</div>
  <div class="service-label" style="left:240px;top:510px"><b>Social Media Marketing</b>Duis autem vel eum iriure dolor in hendrerit vulputate.</div>
  <div class="service-label" style="left:140px;top:400px"><b>Marketing Material &amp; Print Design</b>Duis autem vel eum iriure dolor in hendrerit.</div>
  <div class="service-label" style="left:190px;top:290px"><b>Outsourcing Management</b>Duis autem vel eum iriure dolor in hendrerit vulputate.</div>
</section>

<section class="plans">
  <h2 class="section-title">Select Your Plan</h2>
  <div class="placeholder wood" role="img" aria-label="Wooden floor backdrop"></div>
  <div class="plan featured" style="left:158px">
    <div class="plan-icon"><svg width="22" height="22" viewBox="0 0 24 24" fill="#1b6fb8"><path d="M4 20 16 8l4 4L8 24z"/></svg></div>
    <h3>Basic Plan</h3><p class="from">Starting from</p>
    <p class="price"><sup>$</sup>52<small>.95</small></p>
    <ul><li>Lorem Ipsum Dolar Sipsum</li><li>Lorem Ipsum Dolar</li><li>Lorem Ipsum Dolar Sipsum</li><li>Lorem Ipsum Dolar</li></ul>
    <span class="start">Get Started →</span><span class="more">More Information ➜</span>
  </div>
  <div class="plan" style="left:395px">
    <div class="plan-icon"><svg width="22" height="22" viewBox="0 0 24 24" fill="#1b6fb8"><rect x="4" y="4" width="16" height="16" rx="2"/></svg></div>
    <h3>Standard Plan</h3><p class="from">Starting from</p>
    <p class="price"><sup>$</sup>114<small>.00</small></p>
    <ul><li>Lorem Ipsum Dolar Sipsum</li><li>Lorem Ipsum Dolar</li><li>Lorem Ipsum Dolar Sipsum</li><li>Lorem Ipsum Dolar</li></ul>
    <span class="start">Get Started →</span><span class="more">More Information ➜</span>
  </div>
  <div class="plan" style="left:622px">
    <div class="plan-icon"><svg width="22" height="22" viewBox="0 0 24 24" fill="#f4b400"><circle cx="12" cy="12" r="9"/></svg></div>
    <h3>Gold Plan</h3><p class="from">Starting from</p>
    <p class="price"><sup>$</sup>200<small>.95</small></p>
    <ul><li>Lorem Ipsum Dolar Sipsum</li><li>Lorem Ipsum Dolar</li><li>Lorem Ipsum Dolar Sipsum</li><li>Lorem Ipsum Dolar</li></ul>
    <span class="start">Get Started →</span><span class="more">More Information ➜</span>
  </div>
  <div class="plan" style="left:859px">
    <div class="plan-icon"><svg width="22" height="22" viewBox="0 0 24 24" fill="#1b6fb8"><path d="M12 2l3 7h7l-6 5 2 8-6-5-6 5 2-8-6-5h7z"/></svg></div>
    <h3>Platinum Plan</h3><p class="from">Starting from</p>
    <p class="price"><sup>$</sup>490<small>.00</small></p>
    <ul><li>Lorem Ipsum Dolar Sipsum</li><li>Lorem Ipsum Dolar</li><li>Lorem Ipsum Dolar Sipsum</li><li>Lorem Ipsum Dolar</li></ul>
    <span class="start">Get Started →</span><span class="more">More Information ➜</span>
  </div>
</section>

<section class="video">
  <h2 class="section-title">Watch Video</h2>
  <div class="placeholder video-art" role="img" aria-label="Hands holding a tablet showing a video still"></div>
  <svg class="play" viewBox="0 0 80 80"><circle cx="40" cy="40" r="38" fill="#fff"/><path d="M32 24l24 16-24 16z" fill="#333"/></svg>
</section>

<section class="band">Lorem ipsum dolor sit amet, consectetuer adipiscing elit, sed diam nonummy nibh<br>euismod tincidunt ut laoreet dolore magna aliquam erat volutpat</section>

<section class="clients">
  <h2 class="section-title">Our Clients</h2>
  <p class="lede">Lorem ipsum dolor sit amet, consectetuer adipiscing elit, sed diam nonummy nibh euismod tincidunt ut laoreet dolore magna aliquam erat volutpat. Ut wisi enim ad minim veniam, quis nostrud exerci.</p>
  <span class="client-arrow" style="left:112px">‹</span>
  <div class="client-row">
    <span><i></i>Oakmere</span><span><i></i>Veltrax</span><span><i></i>Veltrax</span><span>Pinewick</span>
    <span><i></i>Oakmere</span><span><i></i>Solvane</span><span>Brindle</span><span>Brindle</span>
  </div>
  <span class="client-arrow" style="left:1072px">›</span>
</section>

<section class="why">
  <h2 class="section-title">Why Choose Us</h2>
  <p class="lede">Lorem ipsum dolor sit amet, consectetuer adipiscing elit, sed diam nonummy nibh euismod tincidunt ut laoreet dolore magna aliquam erat volutpat. Ut wisi enim ad minim veniam, quis nostrud exerci.</p>
  <svg style="position:absolute;left:0;top:0" width="1200" height="505">
    <path d="M430 230 Q600 420 770 230" fill="none" stroke="#9bb4c9" stroke-width="2"/>
    <g fill="#1b6fb8"><circle cx="430" cy="230" r="20" fill="#f47c20"/><circle cx="470" cy="315" r="20"/><circle cx="600" cy="370" r="20"/><circle cx="730" cy="315" r="20"/><circle cx="770" cy="230" r="20"/></g>
  </svg>
  <div class="placeholder why-emblem" role="img" aria-label="Central badge illustration"></div>
  <div class="why-item" style="left:180px;top:210px"><b>100% Risk Free Investment</b>Lorem ipsum dolor sit amet, consectetuer adipiscing elit, sed diam.</div>
  <div class="why-item" style="left:220px;top:305px"><b class="blue">Customer Loyalty Program</b>Lorem ipsum dolor sit amet, consectetuer adipiscing elit, sed diam.</div>
  <div class="why-item" style="left:480px;top:402px"><b class="blue">24/7 U.S. Based Customer Support</b>Lorem ipsum dolor sit amet, consectetuer adipiscing elit, sed diam.</div>
  <div class="why-item" style="left:790px;top:210px"><b>Multiple Payment Options Available</b>Lorem ipsum dolor sit amet, consectetuer adipiscing elit, sed diam.</div>
  <div class="why-item" style="left:750px;top:305px"><b class="blue">Unmatched Personal Service</b>Lorem ipsum dolor sit amet, consectetuer adipiscing elit, sed diam.</div>
</section>

<section class="team">
  <h2 class="section-title">Our Team</h2>
  <p class="lede">Lorem ipsum dolor sit amet, consectetuer adipiscing elit, sed diam nonummy nibh euismod tincidunt ut laoreet dolore magna aliquam erat volutpat. Ut wisi enim ad minim veniam, quis nostrud exerci.</p>
  <span class="client-arrow" style="left:112px;top:220px">‹</span>
  <div class="member" style="left:142px">
    <div class="placeholder photo" role="img" aria-label="Portrait of team member"></div>
    <h4>DANIEL HARTLEY</h4><p class="role">Chief Executive Officer</p>
    <p class="bio">Lorem ipsum dolor sit amet, consectetuer adipiscing elit, sed diam nonummy nibh euismod tincidunt ut laoreet dolore magna… [+]</p>
  </div>
  <div class="member" style="left:630px">
    <div class="placeholder photo" role="img" aria-label="Portrait of team member"></div>
    <h4>OWEN CALDER</h4><p class="role">Chief Operations Officer</p>
    <p class="bio">Lorem ipsum dolor sit amet, consectetuer adipiscing elit, sed diam nonummy nibh euismod tincidunt ut laoreet dolore magna… [+]</p>
  </div>
  <span class="client-arrow" style="left:1072px;top:220px">›</span>
</section>

<section class="inquiry">
  <div class="placeholder inquiry-art" role="img" aria-label="Person typing on a laptop with a coffee cup"></div>
  <h2 class="section-title">Quick Inquiry</h2>
  <div class="form">
    <div class="row"><div class="field">First Name</div><div class="field">Last Name</div></div>
    <div class="row"><div class="field">Email</div><div class="field">Phone Number</div></div>
    <div class="field area">Details About Your Enquiry</div>
    <span class="submit">SUBMIT</span>
  </div>
</section>

<footer class="site-footer">
  <div class="foot-col" style="left:148px"><h5>Quick <span>Links</span></h5>
    <ul><li>Home</li><li>Services</li><li>Pricing</li><li>Our Team</li><li>Success Stories</li><li>Clients</li><li>Contact Us</li></ul></div>
  <div class="foot-col" style="left:338px"><h5>Contact <span>Details</span></h5>
    BrightHarbor.com<br>Street Name, City Name<br>State, Zipcode<br>☎ 555-0142<br>☎ 555-0187<br>✉ hello@brightharbor.com</div>
  <div class="foot-col" style="left:610px"><h5>Newsletter <span>Signup</span></h5>
    Lorem ipsum dolor sit amet,<br>consectetuer adipiscing elit<div class="news-field">Email</div><span class="subscribe">Subscribe</span></div>
  <div class="foot-mark"></div>
  <div class="foot-bar"><span>Copyright © 2017 BrightHarbor.com . All rights reserved</span><span>Terms of Use · Privacy Policy</span></div>
</footer>

</body>
</html>
```